Business Card Design For Office Furniture Clearance Company

Kestrel Office Clearance - our company name pretty much explains what we do, we clear offices for high end clients, mainly plc's and large international companies.

We require a nice looking business card that displays professionalism but without being too serious.

It would be nice to see just a little more than a conventional boring business card, make sure you add some flare.

Industry/Entity Type

Office Furniture

Contact Information for Business Card

CARD 1

Mark Holloway
Director
mark@kestrelofficeclearance.co.uk
m: 07700 153928

t: 01632 960418
www.kestrelofficeclearance.co.uk

Kestrel Office Clearance
Unit K4 B
2-8 Fenwick Lane
Bletchley
Milton Keynes
ZZ9 4QT

free office clearances… you cant get better than that.

CARD 2

Peter Radford
Director
peter@kestrelofficeclearance.co.uk
m: 07700 382615

t: 01632 960418

Kestrel Office Clearance
Unit K4 B
2-8 Fenwick Lane
Bletchley
Milton Keynes
ZZ9 4QT

Font styles to use
Sans Serif

Requirements
Must have
• A white background - as we have a blue logo.
Nice to have
• Nice use of the logo - play around with this and dissect it.

```html
<!DOCTYPE html>
<html lang="en">
<head>
<meta charset="utf-8">
<title>Kestrel Office Clearance – Business Card</title>
<link href="https://fonts.googleapis.com/css2?family=Quicksand:wght@500;700&display=swap" rel="stylesheet">
<style>
  :root{
    --brand-blue:#1b7fc1;
    --brand-deep:#1a62a0;
    --brand-soft:#4c9fd6;
    --paper:#ffffff;
    --stage:#e9ecef;
    --shadow:rgba(20,40,70,.18);
  }
  *{margin:0;padding:0;box-sizing:border-box}
  html,body{width:1200px;height:900px;overflow:hidden}
  body{background:var(--stage);font-family:"Quicksand",sans-serif;position:relative}

  .card{position:absolute;left:250px;width:700px;height:400px;border-radius:26px;overflow:hidden;box-shadow:0 10px 30px var(--shadow)}
  .card--front{top:35px;background:var(--brand-blue)}
  .card--back{top:465px;background:var(--paper)}

  /* front */
  .flame-art{position:absolute;left:-40px;top:110px;width:360px;height:320px;
    background:
      radial-gradient(ellipse 45% 55% at 45% 70%, rgba(255,255,255,.20), rgba(255,255,255,0) 70%),
      radial-gradient(ellipse 30% 45% at 25% 40%, rgba(255,255,255,.12), rgba(255,255,255,0) 70%)}
  .front-mark{position:absolute;left:150px;top:70px;width:460px;height:190px}
  .front-mark__dot{position:absolute;right:0;top:0;width:190px;height:190px;border-radius:50%;background:var(--brand-deep)}
  .front-mark__name{position:absolute;left:0;top:34px;width:380px;color:var(--paper);font-weight:700;font-size:50px;line-height:1.05}
  .front-web{position:absolute;left:220px;top:282px;color:var(--paper);font-weight:700;font-size:15px;letter-spacing:.5px}
  .front-tagline{position:absolute;left:40px;right:40px;bottom:40px;color:var(--paper);font-weight:700;font-size:19px;letter-spacing:.3px;white-space:nowrap}

  /* back */
  .holder{position:absolute;left:34px;top:132px;color:var(--brand-blue)}
  .holder__name{font-weight:700;font-size:27px;letter-spacing:.3px}
  .holder__role{font-weight:700;font-size:14px;letter-spacing:1px;color:var(--brand-deep)}
  .back-mark{position:absolute;right:34px;top:26px;display:flex;flex-direction:column;align-items:flex-end;gap:10px}
  .back-mark__dot{width:100px;height:100px;border-radius:50%;background:var(--brand-blue);margin-right:60px}
  .back-mark__name{color:var(--brand-blue);font-weight:700;font-size:22px}
  .band{position:absolute;left:0;top:0;width:700px;height:400px}
  .address{position:absolute;right:30px;top:212px;text-align:right;color:var(--paper);font-weight:700;font-size:15px;line-height:1.3;font-style:normal}
  .contacts{position:absolute;left:300px;top:300px;list-style:none;color:var(--paper);font-weight:700;font-size:15px;line-height:1.45}
  .contacts li{display:flex;align-items:center;gap:8px}
  .contacts svg{width:13px;height:13px;flex:none}
</style>
</head>
<body>

<section class="card card--front" aria-label="Card front">
  <div class="flame-art" role="img" aria-label="Soft light-blue flame illustration"></div>
  <div class="front-mark">
    <span class="front-mark__dot"></span>
    <span class="front-mark__name">Kestrel Office Clearance</span>
  </div>
  <p class="front-web">www.kestrelofficeclearance.co.uk</p>
  <p class="front-tagline">FREE OFFICE CLEARANCES... YOU CANT GET BETTER THAN THAT</p>
</section>

<section class="card card--back" aria-label="Card back">
  <svg class="band" viewBox="0 0 700 400" aria-hidden="true">
    <rect x="160" y="196" width="540" height="204" fill="var(--brand-blue)"/>
    <circle cx="175" cy="330" r="95" fill="var(--brand-deep)" stroke="var(--paper)" stroke-width="3"/>
  </svg>

  <div class="holder">
    <p class="holder__name">MARK HOLLOWAY</p>
    <p class="holder__role">DIRECTOR</p>
  </div>

  <div class="back-mark">
    <span class="back-mark__dot"></span>
    <span class="back-mark__name">KESTREL OFFICE CLEARANCE</span>
  </div>

  <address class="address">
    Unit K4 B, 2-8 Fenwick Lane,<br>Bletchley,<br>Milton Keynes,<br>ZZ9 4QT
  </address>

  <ul class="contacts">
    <li><svg viewBox="0 0 12 12"><rect x="3" y="0.5" width="6" height="11" rx="1.2" fill="none" stroke="#fff" stroke-width="1.2"/><circle cx="6" cy="9.5" r=".7" fill="#fff"/></svg>07700 153928</li>
    <li><svg viewBox="0 0 12 12"><path d="M2.5 1h2l1 3-1.4 1a6 6 0 0 0 2.9 2.9l1-1.4 3 1v2c0 .8-.6 1.5-1.5 1.5A9.5 9.5 0 0 1 1 2.5C1 1.6 1.7 1 2.5 1z" fill="#fff"/></svg>01632 960418</li>
    <li><svg viewBox="0 0 12 12"><rect x=".7" y="2.2" width="10.6" height="7.6" rx="1" fill="none" stroke="#fff" stroke-width="1.2"/><path d="M1 2.8 6 6.6 11 2.8" fill="none" stroke="#fff" stroke-width="1.2"/></svg>mark@kestrelofficeclearance.co.uk</li>
    <li><svg viewBox="0 0 12 12"><circle cx="6" cy="6" r="5.2" fill="none" stroke="#fff" stroke-width="1.1"/><ellipse cx="6" cy="6" rx="2.2" ry="5.2" fill="none" stroke="#fff" stroke-width="1"/><path d="M1 6h10" stroke="#fff" stroke-width="1"/></svg>www.kestrelofficeclearance.co.uk</li>
  </ul>
</section>

</body>
</html>
```